Quote Cards With KB May 2025 for Instagram

I would like to put these quotes over one of the pictures attached; Instagram (new size: 4:5 (1080 x 1350 pixels) One Quote per picture, and I want the quote to be bold or easy to read as well. I provided a few reference graphics that I really like as examples below. In very small letters at the bottom add @KBHarlowOnline

All of the pictures are attached; you can pick any photo and add one quote to it; but no stock photography

```html
<!DOCTYPE html>
<html lang="en">
<head>
<meta charset="utf-8">
<title>KB Quote Card – 90-Day Plan</title>
<link rel="stylesheet" href="https://fonts.googleapis.com/css2?family=Bebas+Neue&display=swap">
<style>
  :root {
    --stage-pink: #e46fb0;
    --stage-magenta: #c2397f;
    --stage-light: #f3c6df;
    --stage-dark: #2a0d1c;
    --panel-top: rgba(70, 22, 44, 0.72);
    --panel-bottom: rgba(20, 6, 14, 0.82);
    --figure-pink: #d98aad;
    --figure-deep: #b8668c;
    --text-white: #ffffff;
  }
  html, body {
    margin: 0;
    padding: 0;
    width: 960px;
    height: 1200px;
    overflow: hidden;
    background: var(--stage-dark);
  }
  .card {
    position: relative;
    width: 960px;
    height: 1200px;
    overflow: hidden;
    font-family: "Bebas Neue", "Arial Narrow", sans-serif;
    color: var(--text-white);
  }
  .stage-backdrop {
    position: absolute;
    inset: 0;
    background:
      radial-gradient(ellipse at 78% 30%, var(--stage-light) 0%, rgba(243,198,223,0) 55%),
      radial-gradient(ellipse at 0% 40%, var(--stage-pink) 0%, rgba(228,111,176,0) 40%),
      linear-gradient(180deg, var(--stage-magenta) 0%, #d46fa8 45%, #6b2549 78%, var(--stage-dark) 100%);
  }
  .speaker-photo {
    position: absolute;
    left: 622px;
    top: 142px;
    width: 250px;
    height: 1058px;
    border-radius: 110px 110px 40px 40px;
    background: linear-gradient(180deg, var(--figure-pink) 0%, var(--figure-deep) 100%);
    filter: blur(2px);
  }
  .quote-panel {
    position: absolute;
    left: 36px;
    top: 0;
    width: 537px;
    height: 1200px;
    background: linear-gradient(180deg, var(--panel-top) 0%, var(--panel-top) 50%, var(--panel-bottom) 100%);
  }
  .quote {
    position: absolute;
    left: 73px;
    margin: 0;
    font-weight: 400;
    text-transform: uppercase;
    letter-spacing: 0.5px;
  }
  .quote-lead {
    top: 150px;
    font-size: 76px;
    line-height: 76px;
  }
  .quote-promise {
    top: 430px;
    font-size: 76px;
    line-height: 76px;
  }
  .quote-punch {
    top: 806px;
    font-size: 102px;
    line-height: 102px;
  }
  .handle {
    position: absolute;
    left: 73px;
    top: 1106px;
    font-size: 30px;
    line-height: 30px;
    letter-spacing: 0.3px;
  }
</style>
</head>
<body>
  <main class="card">
    <div class="stage-backdrop" role="img" aria-label="Pink stage backdrop with soft lights"></div>
    <div class="speaker-photo" role="img" aria-label="Photo of KB standing in a sparkling pink bodysuit, smiling"></div>
    <div class="quote-panel"></div>

    <p class="quote quote-lead">This 90-day plan<br>helped women<br>over 40 slim down</p>
    <p class="quote quote-promise">Get a tiny waist<br>and feel sexy<br>again.</p>
    <p class="quote quote-punch">You’re next.</p>

    <div class="handle">@KBHarlowOnline</div>
  </main>
</body>
</html>
```